Flyer-Design für Shop für nachhaltige Haustierprodukte
LOMERU
Tolle Umsetzung nach den Vorgaben. Änderungen super und schnell umgesetzt. Gerne wieder!
Zielgruppe
LOMERU ist ein Online-Marktplatz für nachhaltige Haustierprodukte. Meine Zielgruppe sind Frauen zwischen 30 und 60 Jahren mit Haustieren (Hund, Katze, Pferd)
Aufgabenstellung
Das Design soll an der Webseite angepasst sein. Es ist wichtig, dass das Thema Nachhaltigkeit kommuniziert wird und welche Vorteile LOMERU hat (Markenvielvalt, kleine Manufakturen, Handmade etc.)

```html
<!DOCTYPE html>
<html lang="de">
<head>
<meta charset="utf-8">
<title>LOMERU – Flyer</title>
<link href="https://fonts.googleapis.com/css2?family=Montserrat:wght@400;700&display=swap" rel="stylesheet">
<style>
  :root {
    --orange: #ee7a30;
    --ink: #1a1a1a;
    --paper: #ffffff;
    --tick: #8dc26a;
    --photo-light: #9a9a9a;
    --photo-dark: #5e5e5e;
  }
  * { margin: 0; padding: 0; box-sizing: border-box; }
  html, body { width: 1200px; height: 2400px; overflow: hidden; background: var(--paper); }
  .flyer {
    position: relative; width: 1200px; height: 2400px; overflow: hidden;
    background: var(--paper); font-family: "Montserrat", sans-serif; color: var(--ink);
  }
  .hero-photo {
    position: absolute; left: 0; top: 0; width: 1200px; height: 888px;
    background: radial-gradient(ellipse at 55% 45%, var(--photo-light), var(--photo-dark) 85%);
  }
  .brand-box {
    position: absolute; left: 45px; top: 0; width: 336px; height: 402px;
    background: var(--paper);
    display: flex; flex-direction: column; align-items: center; justify-content: flex-end;
    padding-bottom: 34px;
  }
  .brand-box .brand-dot {
    width: 170px; height: 170px; border-radius: 50%;
    border: 5px solid var(--orange); margin-bottom: 52px;
  }
  .brand-name {
    font-weight: 700; font-size: 64px; letter-spacing: 1px; color: var(--orange); line-height: 1;
  }
  .kicker {
    position: absolute; left: 121px; top: 1030px;
    font-size: 42px; font-weight: 400; letter-spacing: 0.5px; line-height: 1;
  }
  .headline {
    position: absolute; left: 118px; top: 1085px;
    font-size: 96px; font-weight: 700; line-height: 102px; color: var(--orange);
    letter-spacing: -0.5px;
  }
  .animal-badges { position: absolute; left: 0; top: 0; }
  .benefits {
    position: absolute; left: 124px; top: 1712px; list-style: none;
  }
  .benefits li {
    display: flex; align-items: center; height: 80px;
    font-size: 44px; font-weight: 400; letter-spacing: 0.3px;
  }
  .benefits svg { width: 50px; height: 50px; margin-right: 46px; flex: none; }
  .footer-band {
    position: absolute; left: 0; top: 2222px; width: 1200px; height: 178px;
    background: var(--orange); display: flex; align-items: center; justify-content: center;
  }
  .web-address { color: var(--paper); font-weight: 700; font-size: 62px; letter-spacing: 0.5px; }
</style>
</head>
<body>
<div class="flyer">
  <div class="hero-photo" role="img" aria-label="Foto: kleiner schwarz-brauner Hund blickt über einen Metallnapf mit Trockenfutter vor grauem Hintergrund"></div>

  <div class="brand-box">
    <div class="brand-dot"></div>
    <div class="brand-name">LOMERU</div>
  </div>

  <p class="kicker">NACHHALTIG LEBEN MIT HAUSTIEREN</p>
  <h1 class="headline">Online-Marktplatz<br>für nachhaltige<br>Tierprodukte</h1>

  <svg class="animal-badges" width="1200" height="2400" viewBox="0 0 1200 2400">
    <g fill="none" stroke="var(--orange)" stroke-width="5">
      <circle cx="191" cy="1534" r="68" role="img" aria-label="Symbol Hund"/>
      <circle cx="373" cy="1534" r="68" role="img" aria-label="Symbol Katze"/>
      <circle cx="554" cy="1534" r="68" role="img" aria-label="Symbol Pferd"/>
    </g>
  </svg>

  <ul class="benefits">
    <li><svg viewBox="0 0 50 50"><circle cx="22" cy="28" r="19" fill="none" stroke="var(--tick)" stroke-width="3.5"/><path d="M13 27l8 9 24-30" fill="none" stroke="var(--tick)" stroke-width="4" stroke-linecap="round" stroke-linejoin="round"/></svg>Marktplatz mit großer Produktauswahl</li>
    <li><svg viewBox="0 0 50 50"><circle cx="22" cy="28" r="19" fill="none" stroke="var(--tick)" stroke-width="3.5"/><path d="M13 27l8 9 24-30" fill="none" stroke="var(--tick)" stroke-width="4" stroke-linecap="round" stroke-linejoin="round"/></svg>Nachhaltiges Futtermittel</li>
    <li><svg viewBox="0 0 50 50"><circle cx="22" cy="28" r="19" fill="none" stroke="var(--tick)" stroke-width="3.5"/><path d="M13 27l8 9 24-30" fill="none" stroke="var(--tick)" stroke-width="4" stroke-linecap="round" stroke-linejoin="round"/></svg>Handgefertigte Accesoires</li>
    <li><svg viewBox="0 0 50 50"><circle cx="22" cy="28" r="19" fill="none" stroke="var(--tick)" stroke-width="3.5"/><path d="M13 27l8 9 24-30" fill="none" stroke="var(--tick)" stroke-width="4" stroke-linecap="round" stroke-linejoin="round"/></svg>Originelles Spielzeug u.v.m.</li>
    <li><svg viewBox="0 0 50 50"><circle cx="22" cy="28" r="19" fill="none" stroke="var(--tick)" stroke-width="3.5"/><path d="M13 27l8 9 24-30" fill="none" stroke="var(--tick)" stroke-width="4" stroke-linecap="round" stroke-linejoin="round"/></svg>Für Hunde, Katzen und Pferde</li>
  </ul>

  <div class="footer-band">
    <span class="web-address">www.lomeru.de</span>
  </div>
</div>
</body>
</html>
```